Garlic Farm for Farm Sales/Restaurant sales

Need a professional, but appealing to agriculture world. We are selling 27 kinds of Organic Garlic from a farm in Simla,CO. I have uploaded logo and business information-we are going to need a template, because I will need to use it for four separate people.
-We are trying to appeal to Farm to table restaurants
-As well as growers/farmers

Target Market(s)

Agriculture Sales/Restaurants-Organic

Industry/Entity Type

Agriculture

Contact Information for Business Card

Want it to look more unique then your average kelto stock card- I want it to look amazing

Font styles to use
Sans Serif

Colors
0455a3
ec1f27
fbed22
ffffff

Requirements
Must have
• Just be creative
Nice to have
• Colorful
Should not have
• plain

```html
<!DOCTYPE html>
<html lang="en">
<head>
<meta charset="utf-8">
<title>Plains Harvest Garlic – Business Card</title>
<link rel="stylesheet" href="https://fonts.googleapis.com/css2?family=Open+Sans:wght@400;600;700&display=swap">
<style>
  :root {
    --stage: #efece8;
    --card-yellow: #fdd800;
    --card-light: #e7e3e3;
    --brand-red: #c8102e;
    --brand-blue: #1c2f63;
    --text-grey: #4a4a4a;
    --edge: #d9d4cf;
    --shadow: rgba(0, 0, 0, 0.22);
  }
  * { box-sizing: border-box; margin: 0; padding: 0; }
  html, body {
    width: 1200px;
    height: 900px;
    overflow: hidden;
    background: var(--stage);
    font-family: "Open Sans", Arial, sans-serif;
  }
  .canvas {
    width: 1200px;
    height: 900px;
    display: flex;
    align-items: center;
    justify-content: center;
    gap: 36px;
  }
  .card {
    position: relative;
    width: 546px;
    height: 312px;
    box-shadow: 0 2px 0 var(--edge), 0 4px 0 var(--edge), 0 12px 26px var(--shadow);
  }

  /* Front */
  .card-front {
    background: var(--card-yellow);
    display: flex;
    flex-direction: column;
    align-items: center;
    justify-content: center;
    gap: 16px;
  }
  .brand-dot {
    border-radius: 50%;
    background: var(--brand-red);
  }
  .card-front .brand-dot {
    width: 86px;
    height: 86px;
  }
  .brand-name {
    font-weight: 700;
    color: var(--brand-blue);
    white-space: nowrap;
  }
  .card-front .brand-name {
    font-size: 32px;
    letter-spacing: 0.3px;
  }

  /* Back */
  .card-back {
    background: var(--card-light);
  }
  .back-mark {
    position: absolute;
    left: 48px;
    top: 62px;
    width: 190px;
    display: flex;
    flex-direction: column;
    align-items: center;
    gap: 12px;
  }
  .back-mark .brand-dot {
    width: 150px;
    height: 150px;
  }
  .back-mark .brand-name {
    font-size: 14px;
  }
  .details {
    position: absolute;
    left: 296px;
    top: 50px;
    color: var(--text-grey);
  }
  .person-name {
    font-weight: 700;
    font-size: 17px;
    line-height: 22px;
    color: var(--brand-red);
  }
  .person-role {
    font-size: 12px;
    line-height: 16px;
    margin-left: 8px;
  }
  .contact-list {
    list-style: none;
    margin-top: 16px;
    margin-left: 20px;
    font-size: 13px;
    line-height: 19px;
  }
  .contact-list li {
    display: flex;
    align-items: center;
    gap: 8px;
  }
  .contact-list svg {
    width: 10px;
    height: 10px;
    fill: var(--brand-red);
    flex-shrink: 0;
  }
  .contact-list .icon-link {
    fill: none;
    stroke: var(--brand-red);
    stroke-width: 1.4;
  }
  .address {
    margin-top: 16px;
    margin-left: 38px;
    font-size: 13px;
    line-height: 19px;
  }
</style>
</head>
<body>
<main class="canvas">
  <section class="card card-front" aria-label="Card front">
    <div class="brand-dot"></div>
    <div class="brand-name">Plains Harvest Garlic</div>
  </section>

  <section class="card card-back" aria-label="Card back">
    <div class="back-mark">
      <div class="brand-dot"></div>
      <div class="brand-name">Plains Harvest Garlic</div>
    </div>

    <div class="details">
      <p class="person-name">Daniel Carver</p>
      <p class="person-role">Managing Director</p>

      <ul class="contact-list">
        <li>
          <svg viewBox="0 0 10 10" aria-hidden="true"><path d="M2 1h2l1 2-1.2 1a5 5 0 0 0 2.2 2.2L7 5l2 1v2a1 1 0 0 1-1 1A7 7 0 0 1 1 2a1 1 0 0 1 1-1z"/></svg>
          (044) 123 456 789
        </li>
        <li>
          <svg viewBox="0 0 10 10" aria-hidden="true"><rect x="1" y="3" width="8" height="6" rx="1"/><rect x="3" y="1" width="4" height="3"/></svg>
          (044) 123456789
        </li>
        <li>
          <svg viewBox="0 0 10 10" aria-hidden="true"><path d="M1 2h8v6H1z"/><path d="M1 2l4 3 4-3" fill="none" stroke="#fff" stroke-width="0.8"/></svg>
          hello@plainsharvest.com
        </li>
        <li>
          <svg class="icon-link" viewBox="0 0 10 10" aria-hidden="true"><path d="M4 6l2-2M3 5L1.5 6.5a1.5 1.5 0 0 0 2 2L5 7M7 5l1.5-1.5a1.5 1.5 0 0 0-2-2L5 3"/></svg>
          www.plainsharvest.com
        </li>
      </ul>

      <p class="address">1234, Address Goes Here,<br>Country, 12345</p>
    </div>
  </section>
</main>
</body>
</html>
```